business card deign

Logo needs the following on it.
1. attached logo
2. Tagline - "If it keeps a drink cold or the party going...we do it!"
3. Name- Dalton Pikes, Founder and CPO
4. Address - 412 E. Carver Avenue, Ste 2207, Tampa, FL. 33917
5. Phone - 555.318.4726

```html
<!DOCTYPE html>
<html lang="en">
<head>
<meta charset="utf-8">
<title>Chillby Business Card</title>
<link rel="stylesheet" href="https://fonts.googleapis.com/css2?family=Open+Sans:wght@400;600;700&display=swap">
<style>
  :root {
    --backdrop: #242424;
    --card: #141414;
    --ink: #ffffff;
    --ink-soft: #e8e8e8;
    --shadow: rgba(0, 0, 0, 0.55);
  }
  html, body {
    margin: 0;
    padding: 0;
    width: 1200px;
    height: 711px;
    overflow: hidden;
    background: var(--backdrop);
  }
  .canvas {
    position: relative;
    width: 1200px;
    height: 711px;
    display: flex;
    align-items: center;
    justify-content: center;
    gap: 48px;
    font-family: "Open Sans", Arial, sans-serif;
    color: var(--ink);
  }
  .card {
    position: relative;
    width: 520px;
    height: 297px;
    background: var(--card);
    border-radius: 22px;
    box-shadow: 0 14px 30px var(--shadow);
    overflow: hidden;
  }
  .brand {
    display: flex;
    align-items: center;
    gap: 14px;
    font-weight: 700;
    letter-spacing: 0.32em;
    text-transform: uppercase;
    color: var(--ink);
  }
  .brand-dot {
    width: 14px;
    height: 14px;
    background: var(--ink);
    border-radius: 50%;
    flex: none;
  }
  .card-front .brand {
    position: absolute;
    left: 50%;
    top: 50%;
    transform: translate(-50%, -50%);
    font-size: 46px;
  }
  .card-front .brand-dot {
    width: 22px;
    height: 22px;
  }
  .card-back .brand {
    position: absolute;
    right: 30px;
    top: 36px;
    font-size: 24px;
  }
  .contact {
    position: absolute;
    left: 36px;
    bottom: 30px;
    padding-left: 22px;
  }
  .contact-bar {
    position: absolute;
    left: 0;
    top: 10px;
    width: 10px;
    height: 52px;
    background: var(--ink);
  }
  .person-name {
    margin: 0;
    font-size: 22px;
    font-weight: 700;
    line-height: 1.15;
  }
  .person-role {
    margin: 0 0 10px;
    font-size: 13px;
    font-weight: 600;
    color: var(--ink-soft);
  }
  .tagline {
    margin: 0 0 10px;
    font-size: 12.5px;
    line-height: 1.35;
    color: var(--ink-soft);
  }
  .detail-list {
    list-style: none;
    margin: 0;
    padding: 0;
    font-size: 12.5px;
    line-height: 1.35;
    color: var(--ink-soft);
  }
  .detail {
    display: flex;
    align-items: flex-start;
    gap: 8px;
  }
  .detail svg {
    width: 12px;
    height: 12px;
    margin-top: 3px;
    flex: none;
  }
</style>
</head>
<body>
<main class="canvas">
  <section class="card card-front" aria-label="Card front">
    <div class="brand"><span class="brand-dot"></span>Chillby</div>
  </section>

  <section class="card card-back" aria-label="Card back">
    <div class="brand"><span class="brand-dot"></span>Chillby</div>
    <div class="contact">
      <span class="contact-bar"></span>
      <h1 class="person-name">Dalton Pikes</h1>
      <p class="person-role">Founder and CPO</p>
      <p class="tagline">If it keeps a drink cold or<br>the party going...we do it!</p>
      <ul class="detail-list">
        <li class="detail">
          <svg viewBox="0 0 24 24" fill="none" stroke="currentColor" stroke-width="2" stroke-linecap="round" stroke-linejoin="round" aria-hidden="true">
            <path d="M22 16.9v3a2 2 0 0 1-2.2 2 19.8 19.8 0 0 1-8.6-3.1 19.5 19.5 0 0 1-6-6A19.8 19.8 0 0 1 2.1 4.2 2 2 0 0 1 4.1 2h3a2 2 0 0 1 2 1.7c.1 1 .4 1.9.7 2.8a2 2 0 0 1-.5 2.1L8 9.9a16 16 0 0 0 6 6l1.3-1.3a2 2 0 0 1 2.1-.4c.9.3 1.8.6 2.8.7a2 2 0 0 1 1.7 2z"/>
          </svg>
          <span>555.318.4726</span>
        </li>
        <li class="detail">
          <svg viewBox="0 0 24 24" fill="none" stroke="currentColor" stroke-width="2" stroke-linecap="round" stroke-linejoin="round" aria-hidden="true">
            <path d="M20 10c0 6-8 12-8 12s-8-6-8-12a8 8 0 0 1 16 0z"/>
            <circle cx="12" cy="10" r="3"/>
          </svg>
          <span>412 E. Carver Avenue,<br>Ste 2207, Tampa, FL. 33917</span>
        </li>
      </ul>
    </div>
  </section>
</main>
</body>
</html>
```